Tidewell Homecare

I am looking to have a website designed for a housekeeping company that looks similar to this one. https://marloweshomecare.example/

I need 5 websites designed but will start with this one to see how I like it.

Industry/Entity Type

House Cleaning

Coding

Coded - Design and coding required

Number of Pages Required

5+ page

Font styles to use
Serif
Script

Colors
ffffff
fdf9cf
fbf289
fbee3f
d6edf3
86cae7
33a6d7
edf1f8
cedeed

```html
<!DOCTYPE html>
<html lang="en">
<head>
<meta charset="utf-8">
<title>Tidewell Homecare – Website Design</title>
<link rel="stylesheet" href="https://fonts.googleapis.com/css2?family=Montserrat:wght@300;400;500;600;700&display=swap">
<style>
:root{
  --blue:#33a6d7;
  --blue-light:#86cae7;
  --blue-pale:#d6edf3;
  --yellow:#fbf289;
  --yellow-pale:#fdf9cf;
  --yellow-strong:#fbee3f;
  --white:#ffffff;
  --board:#f1f1f1;
  --ink:#2a2a2a;
  --muted:#6f6f6f;
  --line:#cfcfcf;
  --dark:#2c3034;
}
*{box-sizing:border-box;margin:0;padding:0}
html,body{width:1200px;height:2824px;overflow:hidden}
body{font-family:"Montserrat",sans-serif;background:var(--board);color:var(--ink);position:relative}

/* board */
.board-band{position:absolute;left:0;top:0;width:1200px;height:674px;background:var(--blue)}
.board-title{position:absolute;top:52px;left:0;width:1200px;text-align:center;color:var(--white);font-weight:600;line-height:1}
.board-title .name{display:block;font-size:80px;letter-spacing:1px}
.board-title .sub{display:block;font-size:40px;font-weight:300;margin-top:8px;letter-spacing:1px}
.board-divider{position:absolute;top:883px;left:375px;width:450px;height:10px}
.board-divider::before,.board-divider::after{content:"";position:absolute;top:5px;height:1px;width:202px;background:#8a8a8a}
.board-divider::before{left:0}.board-divider::after{right:0}
.board-divider .dot{position:absolute;left:220px;top:0;width:10px;height:10px;border-radius:50%;background:var(--blue)}

.page{position:absolute;background:var(--white);overflow:hidden;box-shadow:0 4px 18px rgba(0,0,0,.08)}
.page-preview{left:242px;top:250px;width:716px;height:367px;box-shadow:0 10px 40px rgba(0,0,0,.25)}
.page-desktop{left:368px;top:979px;width:716px;height:1711px}
.page-mobile{left:113px;top:979px;width:168px;height:1711px}
.section{position:relative;width:100%}

.photo{position:absolute}
.btn{position:absolute;display:flex;align-items:center;justify-content:center;font-weight:500}
.btn-blue{background:var(--blue);color:var(--white)}
.btn-white{background:var(--white);color:var(--ink)}
.logo{position:absolute;color:var(--blue);font-weight:600;line-height:1}
.p{color:var(--muted);line-height:1.65}

/* desktop */
.d-header{height:46px;border-bottom:1px solid #eee}
.d-header .logo{left:111px;top:9px;font-size:19px}
.d-header .logo small{display:block;font-size:9px;margin-top:1px}
.d-nav{position:absolute;left:316px;top:18px;display:flex;gap:12px;font-size:7px;color:var(--ink)}
.d-header .btn{left:526px;top:12px;width:78px;height:22px;border:1px solid var(--blue);color:var(--blue);font-size:6.5px}
.d-hero{height:321px}
.d-hero .photo{inset:0;background:linear-gradient(100deg,#b98d5e 0%,#e7dccb 30%,#f5f1ea 55%,#ddd3c3 75%,#8b6a4a 100%)}
.hero-card{position:absolute;background:var(--white);text-align:center}
.d-hero .hero-card{left:204px;top:55px;width:308px;height:200px;padding:30px 30px 0}
.d-hero h1{font-size:19px;font-weight:500;line-height:1.05;color:var(--ink)}
.d-hero .p{font-size:6px;margin-top:14px}
.mouse{display:block;margin:0 auto}
.d-hero .mouse{margin-top:22px}

.d-services{height:226px}
.svc{position:absolute;text-align:center}
.d-services .svc{top:32px;width:190px}
.d-services .svc h3{font-size:9px;font-weight:500;margin-top:12px}
.d-services .svc .p{font-size:6px;margin-top:8px}
.d-services .svc .btn{position:relative;width:97px;height:23px;margin:18px auto 0;font-size:6.5px}
.d-services .vline{position:absolute;left:358px;top:68px;width:1px;height:78px;background:var(--line)}

.d-work{height:221px;background:var(--yellow)}
.d-work .photo{left:0;top:0;width:358px;height:221px;background:linear-gradient(90deg,#c9d6de 0%,#4f83b5 35%,#2f5f9b 55%,#b0735a 80%,#c98d6c 100%)}
.d-work h2{position:absolute;left:398px;top:36px;font-size:15px;font-weight:500}
.d-work .p{position:absolute;left:398px;top:64px;width:200px;font-size:6px;color:#555}
.d-work .btn{left:398px;top:158px;width:97px;height:23px;font-size:6.5px}

.d-estimate{height:229px}
.d-estimate h2{position:absolute;top:38px;width:100%;text-align:center;font-size:15px;font-weight:500}
.form-grid{position:absolute;display:grid}
.d-estimate .form-grid{left:127px;top:82px;width:462px;grid-template-columns:repeat(4,111px);column-gap:6px;row-gap:13px}
.field{position:relative;height:22px;border:1px solid #c9c9c9;color:#999;font-size:6px;padding-left:8px;display:flex;align-items:center}
.field.select::after{content:"";position:absolute;right:8px;top:9px;border:2.5px solid transparent;border-top:3px solid #777}
.field .cal{position:absolute;right:7px;top:6px}
.d-estimate .btn{left:309px;top:161px;width:97px;height:23px;font-size:6.5px}

.vendors{background:var(--yellow-pale)}
.vendor{position:absolute;background:linear-gradient(135deg,#4a4a4a,#1f1f1f)}
.d-vendors{height:212px}
.d-vendors h2{position:absolute;top:38px;width:100%;text-align:center;font-size:15px;font-weight:500}
.d-vendors .vendor{top:79px;width:155px;height:87px}

.testimonial{background:linear-gradient(90deg,#26292c 0%,#363a3e 50%,#3d6f8f 72%,#2f8bc5 85%,#c87a5a 100%)}
.quote-mark{position:absolute;color:var(--white);font-weight:700;line-height:1}
.testimonial .p{position:absolute;color:#e6e6e6}
.testimonial .who{position:absolute;color:var(--white)}
.dots{position:absolute;display:flex}
.dots span{border:1px solid var(--white);border-radius:50%}
.dots span.on{background:var(--white)}
.d-testimonial{height:318px}
.d-testimonial .quote-mark{left:111px;top:80px;font-size:52px}
.d-testimonial .p{left:111px;top:137px;width:240px;font-size:7.5px;line-height:1.75}
.d-testimonial .who{left:111px;top:185px;font-size:11px}
.d-testimonial .dots{left:111px;top:225px;gap:9px}
.d-testimonial .dots span{width:5px;height:5px}

.footer{background:linear-gradient(90deg,#33a6d7,#3aa6dc);color:var(--white)}
.d-footer{height:138px}
.d-footer h4{position:absolute;top:28px;font-size:10px;font-weight:500}
.f-links{position:absolute;font-size:5.5px;line-height:2.4}
.contact-row{display:flex;align-items:center;gap:8px;font-size:5.5px}
.news{position:absolute;background:var(--white);display:flex;align-items:center;color:#999}
.social{position:absolute;border-radius:50%;background:var(--white)}
.copy{position:absolute;font-size:5.5px}

/* mobile */
.m-header{height:30px}
.m-header .logo{left:7px;top:7px;font-size:9px}
.m-header .logo small{display:block;font-size:4.5px}
.burger{position:absolute;right:8px;top:11px;width:9px}
.m-hero{height:237px}
.m-hero .photo{left:0;top:0;width:168px;height:124px;background:linear-gradient(100deg,#b89066,#ece4d8 45%,#f6f2ec 70%,#8a6b4e)}
.m-hero .hero-card{left:8px;top:82px;width:152px;height:137px;padding:16px 8px 0;box-shadow:0 2px 8px rgba(0,0,0,.08)}
.m-hero h1{font-size:9.5px;font-weight:500;line-height:1.15}
.m-hero .p{font-size:4.5px;margin-top:6px}
.m-hero .mouse{margin-top:10px}
.m-services{height:285px}
.m-services .svc{left:8px;width:152px}
.m-services .svc h3{font-size:6.5px;font-weight:500;margin-top:6px}
.m-services .svc .p{font-size:4.5px;margin-top:5px}
.m-services .svc .btn{position:relative;width:78px;height:17px;margin:10px auto 0;font-size:5px}
.m-work-photo{height:104px;background:linear-gradient(90deg,#d5dce2,#4d81b3 40%,#2f5f9b 65%,#b3775e)}
.m-work{height:165px;background:var(--yellow)}
.m-work h2{position:absolute;left:8px;top:16px;font-size:8px;font-weight:500}
.m-work .p{position:absolute;left:8px;top:32px;width:150px;font-size:4.5px;color:#555}
.m-work .btn{left:8px;top:123px;width:78px;height:17px;font-size:5px}
.m-estimate{height:308px}
.m-estimate h2{position:absolute;top:22px;width:100%;text-align:center;font-size:8px;font-weight:500}
.m-estimate .form-grid{left:8px;top:50px;width:152px;grid-template-columns:1fr;row-gap:7px}
.m-estimate .field{height:18px;font-size:4.5px}
.m-estimate .btn{left:45px;top:268px;width:78px;height:17px;font-size:5px}
.m-vendors{height:241px}
.m-vendors h2{position:absolute;top:22px;width:100%;text-align:center;font-size:8px;font-weight:500}
.m-vendors .vendor{left:35px;width:98px;height:55px}
.m-testimonial{height:170px}
.m-testimonial .quote-mark{left:8px;top:30px;font-size:22px}
.m-testimonial .p{left:8px;top:56px;width:100px;font-size:4.5px}
.m-testimonial .who{left:8px;top:112px;font-size:5.5px}
.m-testimonial .dots{left:8px;top:133px;gap:4px}
.m-testimonial .dots span{width:3px;height:3px}
.m-footer{height:171px}
.m-footer h4{position:absolute;top:14px;width:100%;text-align:center;font-size:6.5px;font-weight:500}
.m-footer .news{left:8px;top:33px;width:152px;height:17px;font-size:4.5px;padding-left:8px}
.m-footer .contact{position:absolute;left:8px;top:64px;width:95px;display:flex;flex-direction:column;gap:8px}
.m-footer .contact-row{font-size:4.5px;gap:5px;align-items:flex-start}
.m-footer .f-links{left:113px;top:62px;font-size:4.5px;line-height:2.3}
.m-footer .copy{top:153px;width:100%;text-align:center;font-size:4.5px}
</style>
</head>
<body>

<div class="board-band"></div>
<div class="board-title"><span class="name">Tidewell</span><span class="sub">Homecare</span></div>

<div class="page page-preview">
  <header class="section d-header">
    <div class="logo">Tidewell<small>Homecare</small></div>
    <nav class="d-nav"><span>Services</span><span>Gift Cards</span><span>About</span><span>Contact</span><span>970-555-0148</span></nav>
    <div class="btn">Free Estimate</div>
  </header>
  <section class="section d-hero">
    <div class="photo" role="img" aria-label="Bright clean kitchen and dining room with wooden floor"></div>
    <div class="hero-card">
      <h1>The Importance Of Good<br>Housekeeping</h1>
      <p class="p">Lorem Ipsum is simply dummy text of the printing and typesetting industry. Lorem Ipsum has been the industry's standard dummy text ever since the 1500s, when an unknown printer took a galley of type and scrambled it to make</p>
      <svg class="mouse" width="14" height="20" viewBox="0 0 14 20"><rect x="1" y="1" width="12" height="18" rx="6" fill="none" stroke="#fbee3f" stroke-width="1.3"/><line x1="7" y1="5" x2="7" y2="8" stroke="#fbee3f" stroke-width="1.3"/></svg>
    </div>
  </section>
</div>

<div class="board-divider"><span class="dot"></span></div>

<div class="page page-mobile">
  <header class="section m-header">
    <div class="logo">Tidewell<small>Homecare</small></div>
    <svg class="burger" viewBox="0 0 9 7"><path d="M0 .5h9M0 3.5h9M0 6.5h9" stroke="#33a6d7" stroke-width="1"/></svg>
  </header>
  <section class="section m-hero">
    <div class="photo" role="img" aria-label="Bright clean kitchen interior"></div>
    <div class="hero-card">
      <h1>The Importance Of Good Housekeeping</h1>
      <p class="p">Lorem Ipsum is simply dummy text of the printing and typesetting industry. Lorem Ipsum has been the industry's standard dummy text ever since the 1500s, when an unknown printer took a galley of type and scrambled it to make</p>
      <svg class="mouse" width="10" height="14" viewBox="0 0 14 20"><rect x="1" y="1" width="12" height="18" rx="6" fill="none" stroke="#fbee3f" stroke-width="1.3"/><line x1="7" y1="5" x2="7" y2="8" stroke="#fbee3f" stroke-width="1.3"/></svg>
    </div>
  </section>
  <section class="section m-services">
    <div class="svc" style="top:12px">
      <svg width="42" height="30" viewBox="0 0 42 30"><g fill="none" stroke="#33a6d7" stroke-width="1.2"><rect x="8" y="10" width="26" height="10" rx="3"/><rect x="3" y="13" width="7" height="10" rx="3"/><rect x="32" y="13" width="7" height="10" rx="3"/><rect x="9" y="17" width="24" height="6" rx="2"/><path d="M9 23v3M33 23v3"/><path d="M3 2l2 2M5 2L3 4M8 1v2M8 6v1" stroke="#86cae7"/></g></svg>
      <h3>Residential Cleaning</h3>
      <p class="p">Lorem Ipsum is simply dummy text of the printing and typesetting industry. Lorem Ipsum has been the industry's standard dummy text ever since</p>
      <div class="btn btn-blue">Residencial Services</div>
    </div>
    <div class="svc" style="top:150px">
      <svg width="42" height="30" viewBox="0 0 42 30"><g fill="none" stroke="#33a6d7" stroke-width="1.2"><rect x="10" y="7" width="26" height="17" rx="1.5"/><path d="M10 20h26M23 24v3M18 27h10"/><path d="M4 2l2 2M6 2L4 4M9 1v2" stroke="#86cae7"/></g></svg>
      <h3>Commercial/Office Cleaning</h3>
      <p class="p">Lorem Ipsum is simply dummy text of the printing and typesetting industry. Lorem Ipsum has been the industry's standard dummy text ever since</p>
      <div class="btn btn-blue">Commercial Services</div>
    </div>
  </section>
  <div class="section m-work-photo" role="img" aria-label="Team of cleaning staff in blue uniforms with cleaning equipment"></div>
  <section class="section m-work">
    <h2>Hard Work &amp; Reliability</h2>
    <p class="p">Lorem Ipsum is simply dummy text of the printing and typesetting industry. Lorem Ipsum has been the industry's standard dummy text ever since the 1500s, when an unknown printer took a galley of type and scrambled it to make a type specimen book. It has survived not only five centuries, but also the leap into electronic typesetting, remaining essentially unchanged.</p>
    <div class="btn btn-white">Get To Know Us</div>
  </section>
  <section class="section m-estimate">
    <h2>Free Estimate/Contact Us</h2>
    <div class="form-grid">
      <div class="field">Name*</div>
      <div class="field">Email*</div>
      <div class="field">City*</div>
      <div class="field">Square Footage*</div>
      <div class="field select">Property Type*</div>
      <div class="field select">Type Of Cleaning*</div>
      <div class="field select">Frequency*</div>
      <div class="field">mm/dd/yyyy<svg class="cal" width="7" height="7" viewBox="0 0 8 8"><rect x=".5" y="1.5" width="7" height="6" fill="none" stroke="#888" stroke-width=".8"/><path d="M.5 3.5h7" stroke="#888" stroke-width=".8"/></svg></div>
    </div>
    <div class="btn btn-blue">Submit</div>
  </section>
  <section class="section vendors m-vendors">
    <h2>Preferred Vendors</h2>
    <div class="vendor" style="top:43px" role="img" aria-label="Partner badge"></div>
    <div class="vendor" style="top:103px" role="img" aria-label="Partner badge"></div>
    <div class="vendor" style="top:163px" role="img" aria-label="Partner badge"></div>
  </section>
  <section class="section testimonial m-testimonial" role="img" aria-label="Dark wooden surface with blue rubber gloves, brushes and cleaning bottles">
    <div class="quote-mark">&ldquo;</div>
    <p class="p">Lorem Ipsum is simply dummy text of the printing and typesetting industry. Lorem Ipsum has been the industry's standard dummy text ever since the 1500s.</p>
    <div class="who">— John Doe</div>
    <div class="dots"><span class="on"></span><span></span><span></span></div>
  </section>
  <footer class="section footer m-footer">
    <h4>Newsletter Susbscription</h4>
    <div class="news">Email Address<svg style="position:absolute;right:6px" width="8" height="8" viewBox="0 0 10 10"><path d="M0 5L10 0 7 10 5 6z" fill="#33a6d7"/></svg></div>
    <div class="contact">
      <div class="contact-row"><svg width="6" height="7" viewBox="0 0 8 10"><path d="M4 9.5S1 6 1 4a3 3 0 016 0c0 2-3 5.5-3 5.5z" fill="none" stroke="#fff" stroke-width=".9"/><circle cx="4" cy="4" r="1" fill="#fff"/></svg><span>PO Box 214 | Shore Road,<br>CO 81600</span></div>
      <div class="contact-row"><svg width="7" height="6" viewBox="0 0 10 8"><rect x=".5" y=".5" width="9" height="7" fill="none" stroke="#fff" stroke-width=".9"/><path d="M.5 .5L5 4.5 9.5 .5" fill="none" stroke="#fff" stroke-width=".9"/></svg><span>info@tidewellhomecare<br>.example</span></div>
      <div class="contact-row"><svg width="6" height="6" viewBox="0 0 10 10"><path d="M2 1l2 2-1 1.5c1 1.5 1.5 2 3 3L7.5 6l2 2-1.5 1.5C5 9 1 5 .5 2.5z" fill="none" stroke="#fff" stroke-width=".9"/></svg><span>945-555-0192</span></div>
    </div>
    <div class="f-links">Services<br>Gift Cards<br>About<br>Contact<br>Free Estimate<br>TH LLC Policy</div>
    <div class="social" style="left:115px;top:136px;width:8px;height:8px"></div>
    <div class="copy">© Copyright 2020 Tidewell Homecare</div>
  </footer>
</div>

<div class="page page-desktop">
  <header class="section d-header">
    <div class="logo">Tidewell<small>Homecare</small></div>
    <nav class="d-nav"><span>Services</span><span>Gift Cards</span><span>About</span><span>Contact</span><span>970-555-0148</span></nav>
    <div class="btn">Free Estimate</div>
  </header>
  <section class="section d-hero">
    <div class="photo" role="img" aria-label="Bright clean kitchen and dining room with wooden floor"></div>
    <div class="hero-card">
      <h1>The Importance Of Good<br>Housekeeping</h1>
      <p class="p">Lorem Ipsum is simply dummy text of the printing and typesetting industry. Lorem Ipsum has been the industry's standard dummy text ever since the 1500s, when an unknown printer took a galley of type and scrambled it to make</p>
      <svg class="mouse" width="14" height="20" viewBox="0 0 14 20"><rect x="1" y="1" width="12" height="18" rx="6" fill="none" stroke="#fbee3f" stroke-width="1.3"/><line x1="7" y1="5" x2="7" y2="8" stroke="#fbee3f" stroke-width="1.3"/></svg>
    </div>
  </section>
  <section class="section d-services">
    <div class="svc" style="left:143px">
      <svg width="52" height="40" viewBox="0 0 42 30"><g fill="none" stroke="#33a6d7" stroke-width="1.1"><rect x="8" y="10" width="26" height="10" rx="3"/><rect x="3" y="13" width="7" height="10" rx="3"/><rect x="32" y="13" width="7" height="10" rx="3"/><rect x="9" y="17" width="24" height="6" rx="2"/><path d="M9 23v3M33 23v3"/><path d="M3 2l2 2M5 2L3 4M8 1v2M8 6v1" stroke="#86cae7"/></g></svg>
      <h3>Residential Cleaning</h3>
      <p class="p">Lorem Ipsum is simply dummy text of the printing and typesetting industry. Lorem Ipsum has been the industry's standard dummy text ever since</p>
      <div class="btn btn-blue">Residencial Services</div>
    </div>
    <div class="vline"></div>
    <div class="svc" style="left:387px">
      <svg width="52" height="40" viewBox="0 0 42 30"><g fill="none" stroke="#33a6d7" stroke-width="1.1"><rect x="10" y="7" width="26" height="17" rx="1.5"/><path d="M10 20h26M23 24v3M18 27h10"/><path d="M4 2l2 2M6 2L4 4M9 1v2" stroke="#86cae7"/></g></svg>
      <h3>Commercial/Office Cleaning</h3>
      <p class="p">Lorem Ipsum is simply dummy text of the printing and typesetting industry. Lorem Ipsum has been the industry's standard dummy text ever since</p>
      <div class="btn btn-blue">Commercial Services</div>
    </div>
  </section>
  <section class="section d-work">
    <div class="photo" role="img" aria-label="Team of cleaning staff in blue uniforms with mops, buckets and a vacuum"></div>
    <h2>Hard Work &amp; Reliability</h2>
    <p class="p">Lorem Ipsum is simply dummy text of the printing and typesetting industry. Lorem Ipsum has been the industry's standard dummy text ever since the 1500s, when an unknown printer took a galley of type and scrambled it to make a type specimen book. It has survived not only five centuries, but also the leap into electronic typesetting, remaining essentially unchanged.</p>
    <div class="btn btn-white">Get To Know Us</div>
  </section>
  <section class="section d-estimate">
    <h2>Free Estimate/Contact Us</h2>
    <div class="form-grid">
      <div class="field">Name*</div>
      <div class="field">Email*</div>
      <div class="field">City*</div>
      <div class="field">Square Footage*</div>
      <div class="field select">Property Type*</div>
      <div class="field select">Type Of Cleaning*</div>
      <div class="field select">Frequency*</div>
      <div class="field">mm/dd/yyyy<svg class="cal" width="9" height="9" viewBox="0 0 8 8"><rect x=".5" y="1.5" width="7" height="6" fill="none" stroke="#888" stroke-width=".7"/><path d="M.5 3.5h7" stroke="#888" stroke-width=".7"/></svg></div>
    </div>
    <div class="btn btn-blue">Submit</div>
  </section>
  <section class="section vendors d-vendors">
    <h2>Preferred Vendors</h2>
    <div class="vendor" style="left:112px" role="img" aria-label="Partner badge"></div>
    <div class="vendor" style="left:280px" role="img" aria-label="Partner badge"></div>
    <div class="vendor" style="left:449px" role="img" aria-label="Partner badge"></div>
  </section>
  <section class="section testimonial d-testimonial" role="img" aria-label="Dark wooden surface with blue rubber gloves, brushes and cleaning bottles">
    <div class="quote-mark">&ldquo;</div>
    <p class="p">Lorem Ipsum is simply dummy text of the printing and typesetting industry. Lorem Ipsum has been the industry's standard dummy text ever since the 1500s.</p>
    <div class="who">— &nbsp;John Doe</div>
    <div class="dots"><span class="on"></span><span></span><span></span></div>
  </section>
  <footer class="section footer d-footer">
    <h4 style="left:111px">Quick Links</h4>
    <div class="f-links" style="left:111px;top:50px">Services &nbsp;| &nbsp;Gift Cards &nbsp;| &nbsp;About &nbsp;| &nbsp;Contact<br>| &nbsp;Free Estimate &nbsp;| &nbsp;TH LLC Policy</div>
    <div class="social" style="left:111px;top:93px;width:13px;height:13px"></div>
    <h4 style="left:292px">Contact</h4>
    <div style="position:absolute;left:292px;top:53px;display:flex;flex-direction:column;gap:11px">
      <div class="contact-row"><svg width="8" height="10" viewBox="0 0 8 10"><path d="M4 9.5S1 6 1 4a3 3 0 016 0c0 2-3 5.5-3 5.5z" fill="none" stroke="#fff" stroke-width=".9"/><circle cx="4" cy="4" r="1" fill="#fff"/></svg>PO Box 214 | Shore Road, CO 81600</div>
      <div class="contact-row"><svg width="10" height="8" viewBox="0 0 10 8"><rect x=".5" y=".5" width="9" height="7" fill="none" stroke="#fff" stroke-width=".9"/><path d="M.5 .5L5 4.5 9.5 .5" fill="none" stroke="#fff" stroke-width=".9"/></svg>info@tidewellhomecare.example</div>
      <div class="contact-row"><svg width="9" height="9" viewBox="0 0 10 10"><path d="M2 1l2 2-1 1.5c1 1.5 1.5 2 3 3L7.5 6l2 2-1.5 1.5C5 9 1 5 .5 2.5z" fill="none" stroke="#fff" stroke-width=".9"/></svg>945-555-0192</div>
    </div>
    <h4 style="left:458px">Newsletter Susbscription</h4>
    <div class="news" style="left:458px;top:53px;width:146px;height:22px;font-size:6px;padding-left:11px">Email Address<svg style="position:absolute;right:8px" width="11" height="11" viewBox="0 0 10 10"><path d="M0 5L10 0 7 10 5 6z" fill="#33a6d7"/></svg></div>
    <div class="copy" style="left:458px;top:97px">© Copyright 2020 Tidewell Homecare</div>
  </footer>
</div>

</body>
</html>
```